Web Design Project - Brunnwald Haus

We would like you to refine our web layouts for a (1) homepage and (2) a product page (see attached files for reference).

The client is a swiss construction company, that designs, builds and sells standardized and tailored-made residential houses.

His logo is old, but not up for redesign. The only way to salvage it, is to incorporate its yellow color (as highlight) to the overall design, so as to create some brand awareness.

REQUIREMENTS FOR THE HOMEPAGE:
1. telephone number over menu
2. logo + menu with 6 categories
3. slider for showing various house types (for pics, see attachments)
4. "AKTUELL" card with yellow color (to show his most actual projects) and a strong Call For Action (what in German would be: KONTAKT AUFNEHMEN)
5. a yellow stripe for his company's slogan (Ihr Partner für individuelle und normierte Wohnbauten)
6. A left coloumn with
(a) two picture-holders under the title REFERENZEN
(b) the three supporting logos of TELV, KALDORIS and VB NULLBAU HELVETIA (can be downloaded as pngs)
7. A right column with 6 headlines + texts of 3 lines each
8. a footer with the adress info

REQUIREMENTS FOR PRODUKT PAGE:
1. slider for pictures
2. info box with Call For Action for particular House-types
3. thumbnail pics under the slider for additional images of any particular house type
4. Left-side: name of house type and picture
5. Right-side: Header and blindtext for house description
6. three placeholders for 3 floor plans
Updates

NB No coding necessary. An imaginative, fresh design along the layout requirements will do.
Thanx to all

To all those who had probs with the downloading of the attached files:
we've posted a new Zip.
Have a look!
thankx

Thanks to everyone who participated.
We will be showing a selection of your designs to the client within the next couple of days.
We'll get back to you, as soon as possible.

Industry/Entity Type

Construction

Requirements
Must have
• - slider
- info box with call for action
- thumbnail pictures
- fresh look based on colors, design of elements (slider, info box), font selection

```html
<!DOCTYPE html>
<html lang="de">
<head>
<meta charset="utf-8">
<title>Brunnwald Haus – Wohnbauten</title>
<link rel="stylesheet" href="https://fonts.googleapis.com/css2?family=Arimo:wght@400;700&display=swap">
<style>
:root{
  --yellow:#f6cb1f;
  --yellow-light:#fbe053;
  --yellow-dark:#e8b90f;
  --ink:#222;
  --text:#444;
  --muted:#999;
  --bar:#2a2a2a;
  --line:#dcdcdc;
  --card:#fafafa;
}
*{box-sizing:border-box;margin:0;padding:0}
html,body{width:1016px;height:1200px;overflow:hidden}
body{position:relative;font-family:"Arimo",Arial,sans-serif;color:var(--ink);
  background:linear-gradient(#fdfdfd,#f1f1f1 40%,#f6f6f6)}
.abs{position:absolute}

/* header */
.brand{left:97px;top:32px;font-size:20px;font-weight:700;color:var(--ink);display:flex;align-items:center;gap:8px}
.brand .dot{width:14px;height:14px;background:var(--yellow)}
.phone{right:101px;top:40px;display:flex;align-items:center;gap:8px}
.phone .label{font-size:16px;color:var(--muted)}
.phone .number{font-size:22px;color:#444}

/* nav */
.nav{left:0;top:102px;width:1016px;height:32px;background:var(--bar);display:flex;padding-left:99px}
.nav a{color:#fff;text-decoration:none;font-size:13px;display:flex;align-items:center;justify-content:center;height:32px;position:relative;white-space:nowrap}
.nav a + a::before{content:"";position:absolute;left:0;top:7px;height:18px;border-left:1px solid #555}
.nav .active{background:var(--yellow);color:var(--ink);border-top:2px solid var(--yellow-light)}

/* slider */
.slider{left:97px;top:155px;width:573px;height:278px;background:#fff;border:1px solid var(--line);border-radius:4px;padding:4px}
.slide{width:563px;height:268px;border-radius:3px;position:relative;overflow:hidden;
  background:linear-gradient(180deg,#9fb7cf 0%,#a9b89a 30%,#b8a98c 55%,#c9c2a6 75%,#6f8a4a 100%)}
.slide-bar{position:absolute;left:0;bottom:0;width:100%;height:28px;background:rgba(40,40,40,.75);display:flex;align-items:center;padding:0 6px}
.arrow{width:16px;height:16px;border-radius:50%;background:#fff;margin-right:7px;display:flex;align-items:center;justify-content:center}
.dots{margin-left:auto;display:flex;gap:8px;margin-right:3px}
.dots span{width:11px;height:11px;border-radius:50%;background:var(--yellow)}
.dots span.on{background:#fff}

/* aktuell */
.news{left:689px;top:155px;width:219px;height:261px;background:linear-gradient(#fff,#f2f2f2);border:1px solid var(--line);border-radius:4px}
.news-head{position:absolute;left:4px;top:3px;width:211px;height:36px;border-radius:4px;
  background:linear-gradient(var(--yellow-light),var(--yellow-dark));display:flex;align-items:center;padding-left:7px;gap:9px;font-size:18px;color:#333;letter-spacing:.5px}
.news-head .badge{width:21px;height:21px;border-radius:50%;background:#2a2a2a;border:4px solid #555}
.news ul{list-style:none;position:absolute;left:13px;top:52px;width:192px}
.news li{font-size:11.5px;height:28px;display:flex;align-items:center;gap:6px;border-bottom:1px solid #d8d8d8;white-space:nowrap}
.news li:last-child{border-bottom:none}
.cta{left:709px;top:403px;width:175px;height:30px;border-radius:4px;background:linear-gradient(var(--yellow-light),var(--yellow-dark));
  display:flex;align-items:center;gap:10px;padding-left:8px;font-size:12px;color:#222;box-shadow:0 1px 2px rgba(0,0,0,.2);white-space:nowrap}
.circ{width:16px;height:16px;border-radius:50%;background:#fff;border:1px solid #bbb;display:flex;align-items:center;justify-content:center;flex:none}

/* slogan */
.slogan{left:0;top:452px;width:1016px;height:45px;background:linear-gradient(var(--yellow-light),var(--yellow-dark));
  display:flex;align-items:center;justify-content:center;font-size:22px;color:#222}

/* left column */
.refs{left:97px;top:525px;width:197px;height:487px;background:var(--card);border:1px solid var(--line);border-radius:4px}
.refs h2{position:absolute;left:14px;top:14px;font-size:17px;font-weight:400;color:#333}
.photo{position:absolute;left:13px;width:172px;height:99px;border-radius:2px;border:1px solid #ccc}
.photo.a{top:47px;background:linear-gradient(180deg,#3d5ea8 0%,#6a86c0 40%,#dfe4ea 60%,#6c8a4a 100%)}
.photo.b{top:170px;background:linear-gradient(180deg,#8fb2d8 0%,#cfd8e2 40%,#eeeeee 65%,#7d9a56 100%)}
.btn{position:absolute;height:19px;border-radius:4px;background:linear-gradient(var(--yellow-light),var(--yellow-dark));
  display:inline-flex;align-items:center;gap:4px;padding:0 6px 0 4px;font-size:10.5px;color:#222;white-space:nowrap}
.btn .circ{width:12px;height:12px}
.refs .btn{left:12px;top:286px}
.refs hr{position:absolute;left:11px;top:320px;width:175px;border:none;border-top:1px dotted #999}
.partner{position:absolute;left:50%;transform:translateX(-50%)}

/* right column */
.articles{left:314px;top:525px;width:600px;height:582px;background:var(--card);border:1px solid var(--line);border-radius:4px;padding:11px 11px 0 12px}
.article{height:141px;position:relative}
.article h3{font-size:17px;font-weight:400;color:#333;margin-bottom:7px;white-space:nowrap}
.article p{font-size:10.6px;line-height:15.3px;color:var(--text);width:576px}
.article p span{display:block;white-space:nowrap}
.article .btn{position:relative;margin-top:6px}
.article::after{content:"";position:absolute;left:0;top:130px;width:572px;border-top:1px dotted #999}
.article:last-child::after{display:none}

/* footer */
.footer{left:0;top:1131px;width:1016px;height:69px;background:var(--bar);color:#fff;font-size:10.8px;line-height:17.5px;padding:20px 0 0 102px;white-space:nowrap}
.footer-brand{right:102px;top:1150px;font-size:15px;font-weight:700;color:#fff;display:flex;align-items:center;gap:6px}
.footer-brand .dot{width:10px;height:10px;background:#777}
</style>
</head>
<body>

<header>
  <div class="abs brand"><span class="dot"></span>Brunnwald Haus</div>
  <div class="abs phone">
    <svg width="26" height="28" viewBox="0 0 26 28" aria-hidden="true"><path d="M5 3c3-2 5 0 6 3l-2 3c1 3 3 6 6 8l3-2c3 1 5 3 3 6-2 3-6 4-10 1S3 15 2 10 3 4 5 3z" fill="#f0c21a"/><path d="M16 5a6 6 0 0 1 5 6M16 1a10 10 0 0 1 9 10" stroke="#f0c21a" stroke-width="2" fill="none"/></svg>
    <span class="label">Call us:</span><span class="number">071 480 27 16</span>
  </div>
</header>

<nav class="abs nav">
  <a class="active" style="width:64px">Home</a>
  <a style="width:87px;margin-left:1px">Hauser</a>
  <a style="width:133px">Renovatinen</a>
  <a style="width:123px">Referenzen</a>
  <a style="width:110px">Uber uns</a>
  <a style="width:90px">Kontakt</a>
</nav>

<section class="abs slider">
  <div class="slide" role="img" aria-label="Foto eines zweistöckigen Einfamilienhauses mit Steinfassade und Garage">
    <div class="slide-bar">
      <span class="arrow"><svg width="8" height="8" viewBox="0 0 8 8"><path d="M5 1 2 4l3 3" stroke="#333" stroke-width="1.6" fill="none"/></svg></span>
      <span class="arrow"><svg width="8" height="8" viewBox="0 0 8 8"><path d="M3 1l3 3-3 3" stroke="#333" stroke-width="1.6" fill="none"/></svg></span>
      <div class="dots"><span></span><span class="on"></span><span></span><span></span></div>
    </div>
  </div>
</section>

<aside class="abs news">
  <div class="news-head"><span class="badge"></span>AKTUELL</div>
  <ul>
    <li><svg width="11" height="8" viewBox="0 0 11 8"><rect x="0.5" y="1.5" width="5" height="5" fill="none" stroke="#888"/><path d="M5 4h5M8 2l2 2-2 2" stroke="#e8b90f" stroke-width="1.2" fill="none"/></svg>Bauland in Wolfsried, TG</li>
    <li><svg width="11" height="8" viewBox="0 0 11 8"><rect x="0.5" y="1.5" width="5" height="5" fill="none" stroke="#888"/><path d="M5 4h5M8 2l2 2-2 2" stroke="#e8b90f" stroke-width="1.2" fill="none"/></svg>Bauland in Wolfsried, TG</li>
    <li><svg width="11" height="8" viewBox="0 0 11 8"><rect x="0.5" y="1.5" width="5" height="5" fill="none" stroke="#888"/><path d="M5 4h5M8 2l2 2-2 2" stroke="#e8b90f" stroke-width="1.2" fill="none"/></svg>Bauland in Wolfsried, TG</li>
    <li><svg width="11" height="8" viewBox="0 0 11 8"><rect x="0.5" y="1.5" width="5" height="5" fill="none" stroke="#888"/><path d="M5 4h5M8 2l2 2-2 2" stroke="#e8b90f" stroke-width="1.2" fill="none"/></svg>Bauland in Wolfsried, TG</li>
    <li><svg width="11" height="8" viewBox="0 0 11 8"><rect x="0.5" y="1.5" width="5" height="5" fill="none" stroke="#888"/><path d="M5 4h5M8 2l2 2-2 2" stroke="#e8b90f" stroke-width="1.2" fill="none"/></svg>Bauland in Wolfsried, TG</li>
    <li><svg width="11" height="8" viewBox="0 0 11 8"><rect x="0.5" y="1.5" width="5" height="5" fill="none" stroke="#888"/><path d="M5 4h5M8 2l2 2-2 2" stroke="#e8b90f" stroke-width="1.2" fill="none"/></svg>Bauland in Wolfsried, TG</li>
  </ul>
</aside>
<a class="abs cta"><span class="circ"><svg width="7" height="7" viewBox="0 0 8 8"><path d="M3 1l3 3-3 3" stroke="#333" stroke-width="1.8" fill="none"/></svg></span>KONTAKT AUFNEHMEN</a>

<div class="abs slogan">Ihr Partner für individuelle und normierte Wohnbauten</div>

<aside class="abs refs">
  <h2>Referenzen</h2>
  <div class="photo a" role="img" aria-label="Referenzfoto: weisses Einfamilienhaus mit Balkonen"></div>
  <div class="photo b" role="img" aria-label="Referenzfoto: weisses Haus mit Giebeldach und Garten"></div>
  <a class="btn"><span class="circ"><svg width="6" height="6" viewBox="0 0 8 8"><path d="M3 1l3 3-3 3" stroke="#333" stroke-width="2" fill="none"/></svg></span>Read More</a>
  <hr>
  <div class="partner" style="top:335px;width:97px;height:45px;background:#e3e3e3;border-radius:3px" role="img" aria-label="Partnerzeichen TELV"></div>
  <div class="partner" style="top:394px;width:128px;height:30px;background:#dadada;border-radius:3px" role="img" aria-label="Partnerzeichen KALDORIS"></div>
  <div class="partner" style="top:434px;width:131px;height:20px;background:#e6e6e6;border-radius:3px" role="img" aria-label="Partnerzeichen VB NULLBAU HELVETIA"></div>
</aside>

<main class="abs articles">
  <article class="article">
    <h3>Bearatun and Betreuung</h3>
    <p><span>simply dummy text of the printing and typesetting industry. Lorem Ipsum has been the industry's standard dummy text</span><span>ever since the 1500s, when an unknown printer took a galley of type and scrambled it to make a type specimen book.</span><span>It has survived not only five centuries, but also the leap into electronic typesetting, remaining essentially unchanged.</span><span>It was popularised in the 1960s with the release of Letraset sheets containing.</span></p>
    <a class="btn"><span class="circ"><svg width="6" height="6" viewBox="0 0 8 8"><path d="M3 1l3 3-3 3" stroke="#333" stroke-width="2" fill="none"/></svg></span>Read More</a>
  </article>
  <article class="article">
    <h3>Bearatun and Betreuung</h3>
    <p><span>simply dummy text of the printing and typesetting industry. Lorem Ipsum has been the industry's standard dummy text</span><span>ever since the 1500s, when an unknown printer took a galley of type and scrambled it to make a type specimen book.</span><span>It has survived not only five centuries, but also the leap into electronic typesetting, remaining essentially unchanged.</span><span>It was popularised in the 1960s with the release of Letraset sheets containing.</span></p>
    <a class="btn"><span class="circ"><svg width="6" height="6" viewBox="0 0 8 8"><path d="M3 1l3 3-3 3" stroke="#333" stroke-width="2" fill="none"/></svg></span>Read More</a>
  </article>
  <article class="article">
    <h3>Bearatun and Betreuung</h3>
    <p><span>simply dummy text of the printing and typesetting industry. Lorem Ipsum has been the industry's standard dummy text</span><span>ever since the 1500s, when an unknown printer took a galley of type and scrambled it to make a type specimen book.</span><span>It has survived not only five centuries, but also the leap into electronic typesetting, remaining essentially unchanged.</span><span>It was popularised in the 1960s with the release of Letraset sheets containing.</span></p>
    <a class="btn"><span class="circ"><svg width="6" height="6" viewBox="0 0 8 8"><path d="M3 1l3 3-3 3" stroke="#333" stroke-width="2" fill="none"/></svg></span>Read More</a>
  </article>
  <article class="article">
    <h3>Bearatun and Betreuung</h3>
    <p><span>simply dummy text of the printing and typesetting industry. Lorem Ipsum has been the industry's standard dummy text</span><span>ever since the 1500s, when an unknown printer took a galley of type and scrambled it to make a type specimen book.</span><span>It has survived not only five centuries, but also the leap into electronic typesetting, remaining essentially unchanged.</span><span>It was popularised in the 1960s with the release of Letraset sheets containing.</span></p>
    <a class="btn"><span class="circ"><svg width="6" height="6" viewBox="0 0 8 8"><path d="M3 1l3 3-3 3" stroke="#333" stroke-width="2" fill="none"/></svg></span>Read More</a>
  </article>
</main>

<footer class="abs footer">
  Brunnwald Haus GmbH Fam. Keller<br>
  Lindenweg 14 CH-8357 Tannegg , Tel . 071 480 2716&nbsp; Fax . 071 480 2717
</footer>
<div class="abs footer-brand"><span class="dot"></span>Brunnwald Haus</div>

</body>
</html>
```